New Business Card Design Project

Use the flyer uploaded and website www.brightoakbuilders.com for inspiration.
List Our Services on Backside of business cards
Marcus Delling
Harborline Builders Inc.
Licensed General Contractors
858-471-6093

Contact Information for Business Card

Use the flyer uploaded and website www.brightoakbuilders.com for inspiration. List Our Services on Backside of business cards Marcus Delling Harborline Builders Inc. Licensed General Contractors 858-471-6093

```html
<!DOCTYPE html>
<html lang="en">
<head>
<meta charset="utf-8">
<title>Harborline Builders Business Card</title>
<link href="https://fonts.googleapis.com/css2?family=Cinzel:wght@400;700&family=Montserrat:wght@400&display=swap" rel="stylesheet">
<style>
  :root {
    --backdrop: #2a2a2c;
    --card: #141416;
    --ink: #f4f4f4;
    --rule: #d9d9d9;
  }
  * { margin: 0; padding: 0; box-sizing: border-box; }
  html, body { width: 1200px; height: 912px; overflow: hidden; background: var(--backdrop); }
  .stage { position: relative; width: 1200px; height: 912px; }
  .card {
    position: absolute;
    width: 600px; height: 343px;
    background: var(--card);
    border-radius: 16px;
    color: var(--ink);
    font-family: "Montserrat", sans-serif;
    box-shadow: 0 18px 40px rgba(0,0,0,.55);
  }
  .card--front { left: 120px; top: 70px; }
  .card--back { left: 480px; top: 500px; }

  .brand { display: flex; align-items: center; gap: 12px; }
  .brand__mark { width: 14px; height: 14px; border: 1.5px solid var(--ink); }
  .brand__name { font-family: "Cinzel", serif; font-weight: 400; font-size: 26px; letter-spacing: 1px; color: var(--ink); }

  .card--front .brand { position: absolute; left: 0; right: 0; top: 110px; justify-content: center; }
  .services { position: absolute; left: 0; right: 0; top: 210px; text-align: center; font-size: 17px; line-height: 1.6; letter-spacing: .2px; }

  .card--back .brand { position: absolute; right: 40px; top: 60px; }
  .card--back .brand__name { font-size: 22px; }
  .divider { position: absolute; left: 40px; right: 40px; top: 168px; height: 1px; background: var(--rule); }
  .person { position: absolute; left: 40px; top: 104px; }
  .person__name { font-family: "Cinzel", serif; font-weight: 700; font-size: 26px; line-height: 1.1; letter-spacing: .5px; }
  .person__role { font-size: 16px; margin-top: 2px; }
  .company { position: absolute; right: 40px; top: 186px; font-size: 15px; }
  .contacts { position: absolute; left: 40px; top: 200px; list-style: none; font-size: 16px; line-height: 1.9; }
  .contacts li { display: flex; align-items: center; gap: 10px; }
  .contacts svg { width: 14px; height: 14px; flex: none; }
</style>
</head>
<body>
<main class="stage">
  <section class="card card--front" aria-label="Card front with services">
    <div class="brand">
      <span class="brand__mark"></span>
      <span class="brand__name">HARBORLINE BUILDERS</span>
    </div>
    <p class="services">
      Painting • Flooring • Kitchens • Custom Renovations<br>
      Bathrooms • Energy Efficienct Upgrades
    </p>
  </section>

  <section class="card card--back" aria-label="Card back with contact details">
    <div class="brand">
      <span class="brand__mark"></span>
      <span class="brand__name">HARBORLINE BUILDERS</span>
    </div>
    <div class="person">
      <h1 class="person__name">MARCUS DELLING</h1>
      <p class="person__role">Licensed General Contractors</p>
    </div>
    <div class="divider"></div>
    <p class="company">Harborline Builders Inc.</p>
    <ul class="contacts">
      <li>
        <svg viewBox="0 0 16 16" aria-hidden="true"><path fill="#f4f4f4" d="M3 1.5l2.5 0 1.2 3.2-1.6 1.1a8 8 0 0 0 5.1 5.1l1.1-1.6 3.2 1.2v2.5c0 .8-.7 1.5-1.5 1.5C6.8 14.5 1.5 9.2 1.5 3c0-.8.7-1.5 1.5-1.5z"/></svg>
        858-471-6093
      </li>
      <li>
        <svg viewBox="0 0 16 16" aria-hidden="true"><rect x="1" y="3" width="14" height="10" fill="#f4f4f4"/><path d="M1 3l7 6 7-6" fill="none" stroke="#141416" stroke-width="1.2"/></svg>
        info@brightoakbuilders.com
      </li>
      <li>
        <svg viewBox="0 0 16 16" aria-hidden="true"><circle cx="8" cy="8" r="7" fill="#f4f4f4"/><path d="M1 8h14M8 1c-3 3-3 11 0 14M8 1c3 3 3 11 0 14" fill="none" stroke="#141416" stroke-width="1"/></svg>
        www.brightoakbuilders.com
      </li>
    </ul>
  </section>
</main>
</body>
</html>
```